Email Signature Block Design for Law Firm

I would like you to create a similar signature block for my law firm . I saw the email signature block attached as image002.png and wanted a similar design for my law firm. I want to be able to swap the portraits for each of my staff from the final design. Our law firm colors are black, gold, white, red.

Industry/Entity Type

Law

Requirements
Nice to have
• i like the red circle in around the photo in the tall oak group design. The Silver Lark Co desgn is what inspired me to have a signature block design for my firm.

```html
<!DOCTYPE html>
<html lang="en">
<head>
<meta charset="utf-8">
<title>Email Signature – The Hale Firm</title>
<link href="https://fonts.googleapis.com/css2?family=Cinzel:wght@500;700&family=Poppins:wght@400;500;600;700&display=swap" rel="stylesheet">
<style>
  :root {
    --backdrop: #c3c3c3;
    --ink: #181818;
    --gold: #d6982e;
    --gold-faint: #2f2718;
    --red: #d1151c;
    --red-dark: #a90f14;
    --white: #ffffff;
  }
  * { margin: 0; padding: 0; box-sizing: border-box; }
  html, body { width: 1200px; height: 366px; overflow: hidden; background: var(--backdrop); }
  .canvas { position: relative; width: 1200px; height: 366px; }
  .signature {
    position: absolute; left: 91px; top: 65px; width: 1018px; height: 235px;
    background: var(--ink); overflow: hidden;
    box-shadow: 0 5px 6px rgba(0,0,0,0.28);
  }
  .gold-band { position: absolute; left: 0; top: 178px; width: 100%; height: 57px; background: var(--gold); }

  .brand { position: absolute; left: 22px; top: 23px; display: flex; align-items: center; gap: 10px; }
  .brand-square { width: 14px; height: 14px; background: var(--gold); }
  .brand-name { font-family: "Cinzel", serif; font-weight: 500; font-size: 20px; color: var(--white); letter-spacing: 0.5px; line-height: 1; }
  .brand-tagline {
    position: absolute; left: 89px; top: 62px; width: 200px;
    display: flex; align-items: center; gap: 5px;
    font-family: "Poppins", sans-serif; font-weight: 600; font-size: 8px; color: var(--white); letter-spacing: 4px; white-space: nowrap;
  }
  .brand-tagline::before, .brand-tagline::after { content: ""; flex: 1; height: 1px; background: var(--white); }

  .person-name { position: absolute; left: 21px; top: 102px; font-family: "Cinzel", serif; font-weight: 700; font-size: 33px; color: var(--white); line-height: 1; letter-spacing: -0.5px; }
  .person-role { position: absolute; left: 21px; top: 133px; font-family: "Poppins", sans-serif; font-size: 18px; color: var(--white); line-height: 1.2; }

  .follow { position: absolute; left: 19px; top: 190px; font-family: "Poppins", sans-serif; font-weight: 500; font-size: 13px; letter-spacing: 3.2px; color: var(--white); }
  .social { position: absolute; left: 191px; top: 191px; display: flex; gap: 14px; }
  .social span { width: 16px; height: 16px; border-radius: 50%; background: var(--ink); }

  .portrait { position: absolute; left: 425px; top: 27px; width: 170px; height: 170px; }

  .contacts { position: absolute; left: 628px; top: 58px; font-family: "Poppins", sans-serif; font-weight: 600; font-size: 16px; color: var(--white); line-height: 1.1; }
  .contact { position: absolute; left: 0; display: flex; align-items: flex-start; white-space: nowrap; }
  .contact svg { width: 20px; height: 20px; margin-right: 15px; flex: none; }
  .contact.phone { top: 0; }
  .contact.address { top: 30px; }
  .contact.email { top: 79px; }
  .contact.address svg { margin-top: 3px; }

  .faint-mark { position: absolute; left: 888px; top: 49px; width: 108px; height: 112px; background: var(--gold-faint); }

  .website { position: absolute; left: 630px; top: 185px; font-family: "Poppins", sans-serif; font-weight: 700; font-size: 22px; letter-spacing: 10px; color: var(--ink); line-height: 1.2; }
</style>
</head>
<body>
<div class="canvas">
  <div class="signature">
    <div class="gold-band"></div>

    <div class="brand">
      <div class="brand-square"></div>
      <div class="brand-name">The Hale Firm, PLLC</div>
    </div>
    <div class="brand-tagline">Attorneys At Law</div>

    <div class="person-name">MARCUS D. HALE</div>
    <div class="person-role">Personal Injury Lawyer</div>

    <div class="follow">FOLLOW US ON</div>
    <div class="social"><span></span><span></span><span></span><span></span><span></span></div>

    <div class="faint-mark"></div>

    <svg class="portrait" viewBox="0 0 170 170">
      <circle cx="85" cy="88" r="80" fill="none" stroke="var(--ink)" stroke-width="3"
              stroke-dasharray="120 400" transform="rotate(40 85 88)"/>
      <circle cx="85" cy="88" r="78" fill="none" stroke="var(--red)" stroke-width="12"
              stroke-dasharray="150 40 230 90" transform="rotate(-95 85 88)"/>
      <circle cx="85" cy="88" r="72" fill="var(--ink)"/>
      <circle cx="85" cy="88" r="69" fill="var(--white)"/>
      <defs>
        <linearGradient id="portraitTone" x1="0" y1="0" x2="0" y2="1">
          <stop offset="0" stop-color="#eeeeee"/>
          <stop offset="1" stop-color="#2a2a2e"/>
        </linearGradient>
      </defs>
      <circle cx="85" cy="88" r="66" fill="url(#portraitTone)" role="img" aria-label="Portrait photo of the attorney in a dark suit"/>
    </svg>

    <div class="contacts">
      <div class="contact phone">
        <svg viewBox="0 0 20 20"><circle cx="10" cy="10" r="10" fill="var(--red)"/><path d="M6.5 5.5l2 .2.8 2.2-1.2 1a6 6 0 0 0 3 3l1-1.2 2.2.8.2 2c-.3.6-1 1-1.7 1A8 8 0 0 1 5.5 7.2c0-.7.4-1.4 1-1.7z" fill="var(--white)"/></svg>
        <span>555-014-2929</span>
      </div>
      <div class="contact address">
        <svg viewBox="0 0 20 20"><circle cx="10" cy="10" r="10" fill="var(--red)"/><path d="M10 4.5a3.8 3.8 0 0 0-3.8 3.8c0 2.8 3.8 7 3.8 7s3.8-4.2 3.8-7A3.8 3.8 0 0 0 10 4.5z" fill="var(--white)"/><circle cx="10" cy="8.3" r="1.4" fill="var(--red)"/></svg>
        <span>412 N Harbor St.Suite 300<br>Bayview, FL 32500</span>
      </div>
      <div class="contact email">
        <svg viewBox="0 0 20 20"><circle cx="10" cy="10" r="10" fill="var(--red)"/><rect x="5" y="6.5" width="10" height="7" fill="var(--white)"/><path d="M5 6.5l5 4 5-4M5 13.5l3.6-3.3M15 13.5l-3.6-3.3" stroke="var(--red)" stroke-width="0.9" fill="none"/></svg>
        <span>info@halefirm.com</span>
      </div>
    </div>

    <div class="website">www.halefirm.com</div>
  </div>
</div>
</body>
</html>
```